Boutique custom software development company needs new business card

Our nearly 20 year old custom software development company would like to better include the fact that we are now providing Bitcoin services. These new services are B2B include education (how to acquire and securely hold Bitcoin) and integrating Bitcoin payments into existing ecommerce sites or other existing systems. Please keep the card clean and simple. Attached is our current design and some other files. vextorial.com

Target Market(s)

businesses owners interested in long term relationship

Industry/Entity Type

Custom software development and Bitcoin

Contact Information for Business Card

Dale Parker, dale@vextorial.com, vextorial.com, (888) 555-VXTRL

Font styles to use
Other font styles liked:
• monospace

Requirements
Must have
• double-sided
Nice to have
• clean and simple
Should not have
• physical address

```html
<!DOCTYPE html>
<html lang="en">
<head>
<meta charset="utf-8">
<title>Vextorial business card</title>
<link rel="stylesheet" href="https://fonts.googleapis.com/css2?family=Courier+Prime:wght@400;700&family=Lato:wght@400;900&display=swap">
<style>
  :root {
    --backdrop: #d8d3cb;
    --card-navy: #131a48;
    --brand-blue: #3f74bb;
    --brand-orange: #f07f23;
    --text-light: #dfe2ec;
    --shadow: rgba(0, 0, 0, 0.35);
  }
  * { box-sizing: border-box; margin: 0; padding: 0; }
  html, body {
    width: 900px;
    height: 1200px;
    overflow: hidden;
    background: var(--backdrop);
  }
  .canvas { position: relative; width: 900px; height: 1200px; }
  .card {
    position: absolute;
    left: 78px;
    width: 744px;
    height: 442px;
    background: var(--card-navy);
    border-radius: 40px;
    box-shadow: 0 8px 18px var(--shadow);
  }
  .card--front { top: 130px; }
  .card--back { top: 638px; height: 440px; }

  .brand-block {
    position: absolute;
    left: 106px;
    top: 78px;
    width: 276px;
    height: 288px;
    background: var(--brand-blue);
    display: flex;
    align-items: center;
    justify-content: center;
  }
  .brand-block__name {
    font-family: "Courier Prime", monospace;
    font-weight: 700;
    font-size: 38px;
    color: #ffffff;
    letter-spacing: 1px;
  }
  .divider {
    position: absolute;
    left: 415px;
    top: 78px;
    width: 2px;
    height: 288px;
    background: var(--brand-orange);
  }
  .contact {
    position: absolute;
    left: 445px;
    top: 92px;
    font-family: "Courier Prime", monospace;
    color: var(--text-light);
  }
  .contact__name {
    font-size: 25px;
    font-weight: 400;
    color: var(--brand-orange);
    letter-spacing: 2px;
    text-transform: uppercase;
    line-height: 30px;
  }
  .contact__list { list-style: none; margin-top: 46px; }
  .contact__item {
    display: flex;
    align-items: center;
    gap: 9px;
    font-size: 14.5px;
    line-height: 24.5px;
  }
  .contact__icon { width: 14px; height: 14px; fill: var(--brand-orange); flex: none; }
  .services {
    list-style: none;
    margin-top: 38px;
    font-size: 14.5px;
    line-height: 25px;
    letter-spacing: 0.4px;
  }

  .back-brand {
    position: absolute;
    top: 108px;
    left: 0;
    width: 100%;
    text-align: center;
    font-family: "Lato", sans-serif;
    font-weight: 900;
    font-size: 114px;
    line-height: 140px;
    color: var(--brand-blue);
    letter-spacing: 3px;
  }
  .back-tagline {
    position: absolute;
    top: 266px;
    left: 0;
    width: 100%;
    text-align: center;
    font-family: "Lato", sans-serif;
    font-weight: 400;
    font-size: 41px;
    color: var(--brand-blue);
    letter-spacing: -1px;
  }
</style>
</head>
<body>
<main class="canvas">
  <section class="card card--front">
    <div class="brand-block"><span class="brand-block__name">vextorial</span></div>
    <div class="divider"></div>
    <div class="contact">
      <h1 class="contact__name">Dale Parker</h1>
      <ul class="contact__list">
        <li class="contact__item">
          <svg class="contact__icon" viewBox="0 0 16 16" aria-hidden="true"><path d="M1 5c0-2 3-3 7-3s7 1 7 3v1h-4V5H5v1H1zM4 7h8l2 7H2z"/><circle cx="8" cy="10.5" r="1.8" fill="#131a48"/></svg>
          (888) 555-VXTRL
        </li>
        <li class="contact__item">
          <svg class="contact__icon" viewBox="0 0 16 16" aria-hidden="true"><path d="M1 4h14v1.2L8 9.5 1 5.2z"/><path d="M1 6.8l7 4.3 7-4.3V13H1z"/></svg>
          dale@vextorial.com
        </li>
        <li class="contact__item">
          <svg class="contact__icon" viewBox="0 0 16 16" aria-hidden="true"><circle cx="8" cy="8" r="7"/><path d="M4 5c2 0 2 2 4 2s1 3-1 3-2 2-2 3C3 11 3 7 4 5zM10 3c1 1 3 1 3 3s-2 1-2 3" fill="#131a48"/></svg>
          www.vextorial.com
        </li>
      </ul>
      <ul class="services">
        <li>Custom Software</li>
        <li>Bitcoin Education</li>
        <li>Bitcoin Payments</li>
      </ul>
    </div>
  </section>

  <section class="card card--back">
    <h2 class="back-brand">VEXTORIAL</h2>
    <p class="back-tagline">developer of custom applications</p>
  </section>
</main>
</body>
</html>
```